Road Construction Company needs business cards

We would like a new business card designed for our business.

We're a road construction company based in Qld, Australia.

Can the business card please have the following information on it.

Name: Warren Halbeck
Position: General Manager
Phone: 0472 915 348
Email: Warren.halbeck@tovrin.com.au
Address: 87 Marrow Ave, Pendlebay, QLD, 4023
Website: www.tovrin.com.au

Visually we'd like the card to be professional and simple.

Attached is our logo.

Our website is www.tovrin.com.au

Target Market(s)

Men aged 25-60

Contact Information for Business Card

As listed in project description

Font styles to use
Serif

Requirements
Must have
• Large logo on back of card

```html
<!DOCTYPE html>
<html lang="en">
<head>
<meta charset="utf-8">
<title>Tovrin Business Card</title>
<link rel="stylesheet" href="https://fonts.googleapis.com/css2?family=Exo+2:wght@400;500;800&display=swap">
<style>
  :root {
    --stage: #1e1e1e;
    --blue-deep: #0654a6;
    --blue-mid: #1a7cc8;
    --blue-light: #2b9ad4;
    --accent: #3aa6dc;
    --white: #ffffff;
  }
  * { margin: 0; padding: 0; box-sizing: border-box; }
  html, body { width: 1200px; height: 1015px; overflow: hidden; }
  body {
    background: var(--stage);
    font-family: "Exo 2", sans-serif;
    position: relative;
  }
  .card {
    position: absolute;
    width: 560px;
    height: 320px;
    overflow: hidden;
    box-shadow: 0 14px 30px rgba(0,0,0,0.55);
  }
  .card-front { left: 90px; top: 110px; }
  .front-fill {
    position: absolute;
    inset: 0;
    background: linear-gradient(160deg, var(--blue-light) 0%, var(--blue-mid) 45%, var(--blue-deep) 100%);
  }
  .brand {
    position: absolute;
    font-weight: 800;
    letter-spacing: 4px;
    text-transform: uppercase;
  }
  .card-front .brand {
    left: 0; right: 0; top: 118px;
    text-align: center;
    font-size: 64px;
    color: var(--white);
  }
  .card-back {
    left: 550px; top: 575px;
    background: var(--white);
  }
  .card-back .brand {
    left: 0; right: 0; top: 42px;
    text-align: center;
    font-size: 60px;
    color: var(--blue-deep);
  }
  .info-band {
    position: absolute;
    left: 0; right: 0; bottom: 0;
    height: 138px;
    background: var(--blue-deep);
    border-top: 4px solid var(--accent);
    color: var(--white);
  }
  .info-band .notch {
    position: absolute;
    left: 50%; top: -4px;
    transform: translateX(-50%);
  }
  .person {
    position: absolute;
    left: 34px; top: 26px;
    text-align: right;
    width: 220px;
  }
  .person-name {
    font-weight: 800;
    font-size: 22px;
    letter-spacing: 1px;
    text-transform: uppercase;
  }
  .person-role { font-size: 15px; margin-top: 2px; }
  .divider {
    position: absolute;
    left: 272px; top: 20px;
    width: 1px; height: 62px;
    background: var(--white);
    opacity: 0.85;
  }
  .contacts {
    position: absolute;
    left: 288px; top: 16px;
    list-style: none;
    font-size: 13.5px;
    line-height: 22px;
  }
  .contacts li { display: flex; align-items: center; gap: 7px; }
  .contacts svg { width: 13px; height: 13px; flex: none; }
  .address {
    position: absolute;
    left: 0; right: 0; bottom: 20px;
    text-align: center;
    font-size: 15px;
  }
</style>
</head>
<body>
  <section class="card card-front">
    <div class="front-fill" role="img" aria-label="Blue gradient background with soft angular light facets"></div>
    <div class="brand">Tovrin</div>
  </section>

  <section class="card card-back">
    <div class="brand">Tovrin</div>
    <div class="info-band">
      <svg class="notch" width="18" height="10" viewBox="0 0 18 10" aria-hidden="true">
        <polygon points="0,0 18,0 9,10" fill="#3aa6dc"/>
      </svg>
      <div class="person">
        <div class="person-name">Warren Halbeck</div>
        <div class="person-role">General Manager</div>
      </div>
      <div class="divider"></div>
      <ul class="contacts">
        <li>
          <svg viewBox="0 0 16 16" aria-hidden="true"><path d="M3 1.5l3 3-1.6 1.8c.9 2 2.3 3.4 4.3 4.3L10.5 9l3 3-2 2.2C6 13.5 2.5 10 1.8 4.5z" fill="#fff"/></svg>
          0472 915 348
        </li>
        <li>
          <svg viewBox="0 0 16 16" aria-hidden="true"><rect x="1" y="3" width="14" height="10" fill="#fff"/><path d="M1 3l7 6 7-6" stroke="#0654a6" stroke-width="1.4" fill="none"/></svg>
          Warren.halbeck@tovrin.com.au
        </li>
        <li>
          <svg viewBox="0 0 16 16" aria-hidden="true"><g fill="none" stroke="#fff" stroke-width="1.3"><circle cx="8" cy="8" r="6.5"/><ellipse cx="8" cy="8" rx="2.8" ry="6.5"/><path d="M1.5 8h13M2.5 5h11M2.5 11h11"/></g></svg>
          www.tovrin.com.au
        </li>
      </ul>
      <div class="address">87 Marrow Ave, Pendlebay, QLD, 4023</div>
    </div>
  </section>
</body>
</html>
```